Velmaro Partners Logo and Business Card Design

We already have the rough logo shape (however please make the lines on the logo much thicker so a dark background is not required to see it) . see photos uploaded.
It needs to be refined with color and digitized and then have a front and back business card layout done.
The services are high vibration healing support through a therapy and feng shui service offering. We want people to Feel Happiness, Feel Prosperity and Feel Peace. (the back of the card would have these phrases on it) So a warm, calm and peaceful feeling card.
We would like the card to use the logo provided (with thicker lines and color added) but below the graphic please use the name "Velmaro Partners" NOT Velmaro.
We also would like to use the colors in the colorized matrix shown in photos (gold and purple) but on the lighter side. Thanks for your time!

Front of Card should include: Logo, with Company Name: Velmaro Partners as part of logo, Name: Tomas Brekke email: tomas@velmaro.example web: www.velmaro.example mobile: 555.018.2264 at bottom of front list Family Constellation | Feng Shui

Back of Card should have the logo and the following listed vertically:

PERSONAL | BUSINESS (Larger size then smaller bullet items below)
*Find Happiness
*Find Prosperity
*Find Peace

Target Market(s)

Target market is both business and personal

Contact Information for Business Card

Front of Card should include: Logo, with Company Name: Velmaro Partners as part of logo, Name: Tomas Brekke email: tomas@velmaro.example web: www.velmaro.example mobile: 555.018.2264 at bottom of front list Family Constellation | Feng Shui ++++ Back of Card should have the logo and the following listed vertically: PERSONAL | BUSINESS (Larger size then smaller bullet items below) *Find Happiness *Find Prosperity *Find Peace

Font styles to use
Sans Serif

Colors

Designer to choose colors to be used in the design.

Requirements
Nice to have
• Nice light contrast color for the back of card background
Should not have
• No dark colored background on Card.

```html
<!DOCTYPE html>
<html lang="en">
<head>
<meta charset="utf-8">
<title>Velmaro Partners – Business Card</title>
<link rel="stylesheet" href="https://fonts.googleapis.com/css2?family=Signika:wght@300;400;600&display=swap">
<style>
  :root {
    --navy: #1f2060;
    --red: #e31e25;
    --white: #ffffff;
    --mist: #ecebf6;
    --ink: #222222;
    --backdrop: #3b3b3d;
  }
  * { margin: 0; padding: 0; box-sizing: border-box; }
  html, body { width: 1200px; height: 1059px; overflow: hidden; }
  body {
    background: var(--backdrop);
    font-family: "Signika", sans-serif;
    position: relative;
  }
  .card { position: absolute; overflow: hidden; }
  .card--front { left: 256px; top: 100px; width: 688px; height: 391px; background: var(--white); }
  .card--back { left: 253px; top: 537px; width: 694px; height: 394px; background: var(--mist); }

  .abs { position: absolute; line-height: 1; white-space: nowrap; }

  .brand-mark { position: absolute; border-radius: 50%; border: 3px solid var(--navy); }
  .card--front .brand-mark { left: 490px; top: 62px; width: 64px; height: 64px; }
  .card--back .brand-mark { left: 305px; top: 108px; width: 80px; height: 80px; }

  .brand-name {
    color: var(--red); font-weight: 600; letter-spacing: 0.3px; text-transform: uppercase;
  }
  .card--front .brand-name { right: 36px; top: 154px; font-size: 32px; }
  .card--back .brand-name { left: 0; right: 0; text-align: center; top: 220px; font-size: 40px; }

  .side-tab { position: absolute; left: 0; top: 202px; width: 15px; height: 46px; background: var(--navy); }
  .person-name { left: 33px; top: 198px; font-size: 38px; font-weight: 600; color: var(--red); }
  .person-role { left: 34px; top: 233px; font-size: 19px; font-weight: 300; color: var(--ink); }
  .rule { position: absolute; left: 106px; top: 244px; width: 546px; height: 1.5px; background: var(--navy); }

  .contact { left: 33px; display: flex; align-items: center; gap: 6px; font-size: 20px; font-weight: 300; color: var(--ink); }
  .contact svg { width: 14px; height: 14px; flex: none; }
  .contact--phone { top: 278px; }
  .contact--email { top: 304px; }
  .contact--web { top: 329px; }

  .service { right: 36px; display: flex; align-items: center; gap: 8px; font-size: 17px; font-weight: 300; color: var(--ink); }
  .service--feng { top: 306px; }
  .service--family { top: 331px; }
  .dot { width: 11px; height: 11px; border-radius: 50%; border: 1.5px solid var(--navy); display: inline-block; }

  .band { position: absolute; left: 0; top: 373px; }

  .segments { top: 303px; left: 0; right: 0; text-align: center; font-size: 17.5px; font-weight: 400; color: var(--red); letter-spacing: 0.3px; }
  .segments-rule { position: absolute; left: 255px; top: 333px; width: 178px; height: 2px; background: var(--red); }
  .promises { top: 347px; left: 0; right: 0; display: flex; justify-content: center; gap: 12px; font-size: 18.5px; font-weight: 300; color: var(--navy); }
  .promise { display: flex; align-items: center; gap: 8px; }
</style>
</head>
<body>

<section class="card card--front" aria-label="Card front">
  <span class="brand-mark" aria-hidden="true"></span>
  <div class="abs brand-name">Velmaro Partners</div>

  <div class="side-tab"></div>
  <div class="abs person-name">Tomas Brekke</div>
  <div class="abs person-role">Owner</div>
  <div class="rule"></div>

  <div class="abs contact contact--phone">
    <svg viewBox="0 0 14 14" aria-hidden="true"><path fill="#e31e25" d="M1 5c0-2 3-3 6-3s6 1 6 3v1.5h-3V5H4v1.5H1zM3 7h8l1.5 5h-11z"/></svg>
    <span>555.018.2264</span>
  </div>
  <div class="abs contact contact--email">
    <svg viewBox="0 0 14 14" aria-hidden="true"><rect x="1" y="3" width="12" height="8.5" rx="1" fill="#e31e25"/><path d="M1.5 4l5.5 4 5.5-4" stroke="#fff" stroke-width="1.2" fill="none"/></svg>
    <span>tomas@velmaro.example</span>
  </div>
  <div class="abs contact contact--web">
    <svg viewBox="0 0 14 14" aria-hidden="true"><circle cx="7" cy="7" r="6" fill="#e31e25"/><path d="M4 4.5c1.5 0 2 1 3 1s.5 2-1 2.5 0 2.5-1 3M9 3c0 1.5 1.5 1 2 2.5s-1 2.5 0 4" stroke="#fff" stroke-width="1" fill="none"/></svg>
    <span>www.velmaro.example</span>
  </div>

  <div class="abs service service--feng"><span>Feng Shui</span><span class="dot"></span></div>
  <div class="abs service service--family"><span>Family Constellation</span><span class="dot"></span></div>

  <svg class="band" width="688" height="18" viewBox="0 0 688 18" aria-hidden="true">
    <polygon points="0,0 351,0 328,18 0,18" fill="#1f2060"/>
    <polygon points="361,0 688,0 688,18 338,18" fill="#e31e25"/>
  </svg>
</section>

<section class="card card--back" aria-label="Card back">
  <span class="brand-mark" aria-hidden="true"></span>
  <div class="abs brand-name">Velmaro Partners</div>
  <div class="abs segments">PERSONAL | BUSINESS</div>
  <div class="segments-rule"></div>
  <div class="abs promises">
    <span class="promise"><span class="dot"></span>Find Happiness</span>
    <span class="promise"><span class="dot"></span>Find Prosperity</span>
    <span class="promise"><span class="dot"></span>Find Peace</span>
  </div>
</section>

</body>
</html>
```